Business Card Design

We need a business card designed for our new company. Prefer a black card with white logo & writing.

Contact Information for Business Card

Ted Galloway, address: 7-4812 Fernhollow Road, Abbotsford, BC, V3K 8R2, Office Phone: 604-712-3390, Cell: 604-947-2164, Email: ted@resinworkshub.ca

Colors

Designer to choose only greyscale colors for use in the design.

```html
<!DOCTYPE html>
<html lang="en">
<head>
<meta charset="utf-8">
<title>Resinworks Hub – Business Card</title>
<link href="https://fonts.googleapis.com/css2?family=Poppins:wght@400;700;800&display=swap" rel="stylesheet">
<style>
  :root {
    --backdrop: #4a4a4a;
    --card: #111111;
    --card-back: #151515;
    --ink: #ffffff;
    --ink-soft: #e6e6e6;
    --pattern-dark: #141414;
    --pattern-light: #2c2c2c;
  }
  * { box-sizing: border-box; margin: 0; padding: 0; }
  html, body {
    width: 1200px; height: 675px; overflow: hidden;
    background: radial-gradient(ellipse at 50% 55%, #5a5a5a 0%, var(--backdrop) 60%, #3a3a3a 100%);
    font-family: "Poppins", sans-serif;
    color: var(--ink);
  }
  .stage {
    position: relative; width: 1200px; height: 675px;
    display: flex; align-items: center; justify-content: center; gap: 60px;
  }
  .card {
    width: 520px; height: 297px; border-radius: 4px;
    position: relative; overflow: hidden;
    box-shadow: 0 14px 30px rgba(0,0,0,.45);
  }
  /* front */
  .card--front { background: var(--card); }
  .front__pattern {
    position: absolute; inset: 0;
    background: linear-gradient(100deg, var(--pattern-dark) 0%, var(--pattern-dark) 45%, var(--pattern-light) 80%, #1d1d1d 100%);
  }
  .front__brand {
    position: absolute; left: 0; right: 0; top: 50%; transform: translateY(-50%);
    display: flex; align-items: center; justify-content: center; gap: 12px;
  }
  .brand-mark { width: 14px; height: 14px; background: var(--ink); }
  .brand-name {
    font-weight: 800; font-size: 34px; letter-spacing: 1px; color: var(--ink);
  }
  /* back */
  .card--back { background: var(--card-back); }
  .back__brand {
    position: absolute; top: 46px; left: 0; right: 0;
    display: flex; align-items: center; justify-content: center; gap: 9px;
  }
  .back__brand .brand-name { font-size: 24px; }
  .back__brand .brand-mark { width: 10px; height: 10px; }
  .back__details {
    position: absolute; top: 118px; left: 0; right: 0;
    display: flex; justify-content: center; align-items: stretch;
  }
  .person { text-align: right; padding-right: 18px; display: flex; flex-direction: column; justify-content: flex-end; padding-bottom: 4px; }
  .person__name { font-weight: 800; font-size: 18px; letter-spacing: .5px; line-height: 1.2; }
  .person__role { font-size: 12px; color: var(--ink-soft); }
  .divider { width: 2px; background: var(--ink); }
  .contacts { list-style: none; padding-left: 16px; display: flex; flex-direction: column; gap: 4px; }
  .contacts li { display: flex; align-items: center; gap: 7px; font-size: 12.5px; letter-spacing: .8px; color: var(--ink-soft); }
  .contacts svg { width: 11px; height: 11px; fill: var(--ink); flex: none; }
  .address {
    position: absolute; bottom: 38px; left: 0; right: 0; text-align: center;
    font-size: 12.5px; letter-spacing: .5px; color: var(--ink-soft);
  }
</style>
</head>
<body>
<main class="stage">
  <section class="card card--front">
    <div class="front__pattern" role="img" aria-label="Repeating pattern of the company mark in dark grey tones"></div>
    <div class="front__brand">
      <span class="brand-mark"></span>
      <span class="brand-name">RESINWORKS HUB</span>
    </div>
  </section>

  <section class="card card--back">
    <div class="back__brand">
      <span class="brand-mark"></span>
      <span class="brand-name">RESINWORKS HUB</span>
    </div>
    <div class="back__details">
      <div class="person">
        <p class="person__name">TED GALLOWAY</p>
        <p class="person__role">Manager</p>
      </div>
      <div class="divider"></div>
      <ul class="contacts">
        <li><svg viewBox="0 0 24 24"><path d="M6.6 10.8a15 15 0 0 0 6.6 6.6l2.2-2.2a1 1 0 0 1 1-.25 11.4 11.4 0 0 0 3.6.6 1 1 0 0 1 1 1V20a1 1 0 0 1-1 1A17 17 0 0 1 3 4a1 1 0 0 1 1-1h3.5a1 1 0 0 1 1 1c0 1.25.2 2.45.6 3.6a1 1 0 0 1-.25 1z"/></svg>604-712-3390</li>
        <li><svg viewBox="0 0 24 24"><path d="M7 1h10a2 2 0 0 1 2 2v18a2 2 0 0 1-2 2H7a2 2 0 0 1-2-2V3a2 2 0 0 1 2-2zm0 3v14h10V4z"/></svg>604-947-2164</li>
        <li><svg viewBox="0 0 24 24"><path d="M2 5h20v14H2zm2 2v.5l8 5 8-5V7z"/></svg>ted@resinworkshub.ca</li>
        <li><svg viewBox="0 0 24 24"><path d="M12 2a10 10 0 1 0 0 20 10 10 0 0 0 0-20zm0 2c1 1.3 1.8 3 2.2 5H9.8C10.2 7 11 5.3 12 4zM4.3 14a8 8 0 0 1 0-4h3.3a16 16 0 0 0 0 4zm5.5 1h4.4c-.4 2-1.2 3.7-2.2 5-1-1.3-1.8-3-2.2-5zm0-5h4.4a14 14 0 0 1 0 4H9.8a14 14 0 0 1 0-4zm6.6 4a16 16 0 0 0 0-4h3.3a8 8 0 0 1 0 4z"/></svg>www.resinworkshub.ca</li>
      </ul>
    </div>
    <p class="address">7-4812 Fernhollow Road, Abbotsford, BC, V3K 8R2</p>
  </section>
</main>
</body>
</html>
```